I need a business card for my original fine art pieces

I would like a business card design including a logo design for a new business in the art world. I am based in the Hunter Valley NSW Australia. I am a contemporary figurative, encaustic and wildlife artist. I would like to be able to upload my email and mobile number to this as well. This design should be one that I can incorporate into banners and flyers etc. Id like to incorporate one of my own images or partial image into the background or somewhere below. My initials are RJ and I would like these used as a logo type. I would like the use of some colour and it to be bright and catchy. The final design should communicate artwork custom made and commissions available.

Overview: Original Fine Artworks for sale, online, art galleries etc, Custom made to order and by commission.

Target market is world wide audience and corporate world

My figurative work is painted using acrylics in a lot of natural ochre colours that reflect the Australian Outback, on canvas, linen, paper or board: My encaustic work is created in a contemporary abstract style using a blow torch and a made with a medium of 100% pure bees wax, Damar resin, mixed media and coloured pigments, applied to Birch board. My wildlife are created using coloured pencil and mixed media on a variety of paper types or board.

```html
<!DOCTYPE html>
<html lang="en">
<head>
<meta charset="utf-8">
<title>Rena Jarvis — Business Card</title>
<link rel="stylesheet" href="https://fonts.googleapis.com/css2?family=Cinzel:wght@500&family=Libre+Baskerville&family=Lato:wght@400&display=swap">
<style>
  :root {
    --backdrop: #2b2b2d;
    --card-light: #fbfbfb;
    --card-dark: #060606;
    --accent: #ea4a28;
    --ink: #161616;
    --paper-text: #f2f2f2;
    --art-dark: #1a1a1a;
    --art-light: #e9e9e9;
  }
  * { margin: 0; padding: 0; box-sizing: border-box; }
  html, body { width: 1200px; height: 900px; overflow: hidden; }
  body { background: var(--backdrop); position: relative; font-family: "Lato", sans-serif; }

  .card {
    position: absolute;
    width: 640px;
    height: 366px;
    border-radius: 26px;
    overflow: hidden;
  }

  /* Front card */
  .card--front { left: 90px; top: 90px; background: var(--card-light); }
  .front__artwork {
    position: absolute; left: 0; top: 0; width: 270px; height: 100%;
    background: linear-gradient(160deg, var(--art-light) 0%, #9a9a9a 40%, var(--art-dark) 75%);
  }
  .front__brand {
    position: absolute; left: 300px; top: 40px; width: 320px;
    display: flex; flex-direction: column; align-items: center;
  }
  .monogram {
    display: flex; align-items: center; justify-content: center;
    border: 4px solid var(--accent); border-radius: 50%;
    font-family: "Cinzel", serif; font-weight: 500; color: var(--accent);
  }
  .monogram--large { width: 160px; height: 160px; font-size: 64px; }
  .front__tagline {
    margin-top: 34px; text-align: center; color: var(--ink);
    font-size: 17px; line-height: 1.35;
  }

  /* Back card */
  .card--back { left: 470px; top: 440px; background: var(--card-dark); }
  .back__brand {
    position: absolute; left: 40px; top: 80px;
    display: flex; flex-direction: column; align-items: center;
  }
  .monogram--small { width: 110px; height: 110px; font-size: 44px; border-width: 3px; }
  .brand__name {
    margin-top: 10px; font-family: "Cinzel", serif; font-weight: 500;
    font-size: 34px; color: var(--accent); letter-spacing: 1px;
  }
  .brand__descriptor {
    font-family: "Lato", sans-serif; font-size: 15px; letter-spacing: 3px;
    color: var(--paper-text);
  }
  .back__contact {
    position: absolute; left: 372px; top: 92px; color: var(--paper-text);
    font-size: 16px; line-height: 1.45;
  }
  .contact__name {
    font-family: "Libre Baskerville", serif; font-size: 25px; color: var(--accent);
    line-height: 1.2;
  }
  .contact__list { list-style: none; margin-top: 2px; }
  .contact__item { display: flex; align-items: center; gap: 10px; }
  .contact__icon { width: 14px; height: 14px; flex: none; }
  .contact__web-name { color: var(--accent); }
</style>
</head>
<body>

  <section class="card card--front">
    <div class="front__artwork" role="img" aria-label="Ink illustration of a fashion figure in a black jacket and pearl necklace"></div>
    <div class="front__brand">
      <div class="monogram monogram--large">RJ</div>
      <p class="front__tagline">
        Original Fine Artworks for sale<br>
        online, art galleries etc<br>
        Custom made to order and by commission.
      </p>
    </div>
  </section>

  <section class="card card--back">
    <div class="back__brand">
      <div class="monogram monogram--small">RJ</div>
      <div class="brand__name">RENA JARVIS</div>
      <div class="brand__descriptor">ORIGINAL FINE ARTWORKS</div>
    </div>

    <div class="back__contact">
      <div class="contact__name">Rena Jarvis</div>
      <div class="contact__role">Director</div>
      <div class="contact__location">Hunter Valley Australia</div>
      <div class="contact__abn">ABN 12 345 678 901</div>
      <ul class="contact__list">
        <li class="contact__item">
          <svg class="contact__icon" viewBox="0 0 14 14" aria-hidden="true">
            <rect x="3.5" y="1" width="7" height="12" rx="1.5" fill="none" stroke="#ea4a28" stroke-width="1.6"/>
            <circle cx="7" cy="10.5" r="0.9" fill="#ea4a28"/>
          </svg>
          <span>+61 400 123 456</span>
        </li>
        <li class="contact__item">
          <svg class="contact__icon" viewBox="0 0 14 14" aria-hidden="true">
            <rect x="1" y="3" width="12" height="8.5" rx="1" fill="none" stroke="#ea4a28" stroke-width="1.5"/>
            <path d="M1.5 3.6 L7 8 L12.5 3.6" fill="none" stroke="#ea4a28" stroke-width="1.5"/>
          </svg>
          <span>rena@jarvisart.com</span>
        </li>
        <li class="contact__item">
          <svg class="contact__icon" viewBox="0 0 14 14" aria-hidden="true">
            <circle cx="7" cy="7" r="5.8" fill="none" stroke="#ea4a28" stroke-width="1.4"/>
            <ellipse cx="7" cy="7" rx="2.6" ry="5.8" fill="none" stroke="#ea4a28" stroke-width="1.2"/>
            <line x1="1.2" y1="7" x2="12.8" y2="7" stroke="#ea4a28" stroke-width="1.2"/>
          </svg>
          <span>www.<span class="contact__web-name">renajarvisart</span>.com</span>
        </li>
      </ul>
    </div>
  </section>

</body>
</html>
```